Business Card Design Project

We are a construction company in Orange County, CA. We need a two sided business card. We would like the back to be our logo with web URL. Front should included Name, title, address, phone, fax and email address.

our address is
627 West Dorrance Blvd, Suite 308
Anaheim, CA 92718

Our logo files are attached.

Construction

```html
<!DOCTYPE html>
<html lang="en">
<head>
<meta charset="utf-8">
<title>Verant Business Card – Front and Back</title>
<link rel="stylesheet" href="https://fonts.googleapis.com/css2?family=Source+Sans+3:wght@400;600;700;900&display=swap">
<style>
  :root {
    --brand-blue: #164a7f;
    --ink-grey: #4a4a4a;
    --rule-dark: #2a2a2a;
    --rule-grey: #b8b8b8;
    --card-white: #ffffff;
    --backdrop: #ecebe8;
    --card-edge: #8c8c8c;
  }
  * { margin: 0; padding: 0; box-sizing: border-box; }
  html, body {
    width: 1200px;
    height: 1085px;
    overflow: hidden;
    background: var(--backdrop);
    font-family: "Source Sans 3", sans-serif;
  }
  .canvas { position: relative; width: 1200px; height: 1085px; }

  .card {
    position: absolute;
    width: 784px;
    height: 447px;
    background: var(--card-white);
    border: 1px solid var(--card-edge);
  }
  .card--front { left: 88px; top: 75px; }
  .card--back  { left: 343px; top: 568px; }

  .wordmark {
    position: absolute;
    left: 0;
    width: 100%;
    text-align: center;
    font-family: "Source Sans 3", sans-serif;
    font-weight: 900;
    font-size: 100px;
    line-height: 1;
    letter-spacing: 0.02em;
    color: var(--brand-blue);
  }
  .card--front .wordmark { top: 52px; }
  .card--back  .wordmark { top: 128px; }

  .address {
    position: absolute;
    right: 414px;
    top: 236px;
    text-align: right;
    font-size: 19px;
    line-height: 26px;
    color: var(--ink-grey);
  }

  .divider {
    position: absolute;
    left: 397px;
    top: 228px;
    width: 1px;
    height: 105px;
    background: var(--rule-grey);
  }

  .contact-list {
    position: absolute;
    left: 431px;
    top: 226px;
    list-style: none;
    font-size: 19px;
    line-height: 25px;
    color: var(--ink-grey);
  }
  .contact-list li { display: flex; align-items: center; gap: 6px; }
  .contact-list svg { width: 15px; height: 15px; fill: var(--ink-grey); flex: none; }

  .footer-rule { position: absolute; top: 368px; height: 4px; }
  .footer-rule--accent { left: 0; width: 37px; background: var(--rule-dark); }
  .footer-rule--main { left: 46px; right: 0; background: var(--brand-blue); }

  .name-line {
    position: absolute;
    top: 397px;
    left: 0;
    width: 100%;
    text-align: center;
    font-size: 25px;
    color: var(--brand-blue);
  }
  .name-line .person-name { font-weight: 700; }

  .web-address {
    position: absolute;
    top: 287px;
    left: 0;
    width: 100%;
    text-align: center;
    font-size: 20px;
    letter-spacing: 0.18em;
    color: var(--ink-grey);
  }
</style>
</head>
<body>
<main class="canvas">

  <section class="card card--front" aria-label="Card front">
    <div class="wordmark">VERANT</div>

    <address class="address" style="font-style: normal;">
      627 West Dorrance Blvd<br>
      Suite 308, Anaheim<br>
      CA&nbsp;&nbsp;92718
    </address>

    <div class="divider"></div>

    <ul class="contact-list">
      <li>
        <svg viewBox="0 0 16 16" aria-hidden="true"><path d="M3.6 1.2l2.3 2.6-1.3 1.8c.9 2 2.6 3.8 4.7 4.8l1.8-1.3 2.6 2.3-1.5 2.4C7.5 13.6 2.4 8.5 1.2 2.7z"/></svg>
        01-555-0142
      </li>
      <li>
        <svg viewBox="0 0 16 16" aria-hidden="true"><path d="M4 1h7l2 2v3h1.5c.8 0 1.5.7 1.5 1.5V14H0V7.5C0 6.7.7 6 1.5 6H4zm1 1v4h7V3.4L10.6 2zM3 9v2h10V9z"/></svg>
        01-555-0143
      </li>
      <li>
        <svg viewBox="0 0 16 16" aria-hidden="true"><path d="M1 3h14v1.2L8 8.5 1 4.2zm0 2.6l7 4.3 7-4.3V13H1z"/></svg>
        info@verantbuild.com
      </li>
      <li>
        <svg viewBox="0 0 16 16" aria-hidden="true"><path d="M8 1a7 7 0 100 14A7 7 0 008 1zm-5.4 6h2.6c.1-1.6.5-3 1.1-4A5.6 5.6 0 002.6 7zm4 0h2.8C9.3 5.3 8.8 3.6 8 2.6 7.2 3.6 6.7 5.3 6.6 7zm4.2 0h2.6A5.6 5.6 0 009.7 3c.6 1 1 2.4 1.1 4zM2.6 9a5.6 5.6 0 003.7 4c-.6-1-1-2.4-1.1-4zm4 0c.1 1.7.6 3.4 1.4 4.4.8-1 1.3-2.7 1.4-4.4zm4.2 0c-.1 1.6-.5 3-1.1 4a5.6 5.6 0 003.7-4z"/></svg>
        www.verantbuild.com
      </li>
    </ul>

    <div class="footer-rule footer-rule--accent"></div>
    <div class="footer-rule footer-rule--main"></div>

    <p class="name-line"><span class="person-name">Your Name,</span> Title</p>
  </section>

  <section class="card card--back" aria-label="Card back">
    <div class="wordmark">VERANT</div>
    <p class="web-address">www.verantbuild.com</p>
  </section>

</main>
</body>
</html>
```